QP Fiduciary Website Redesign Contest

We want to refresh our website to be more insitutional, professional for an international audience. We have designed a new logo for this purpose and that has been attached. A full brand brief and positioning statement has also been attached. Please read through all the documents carefully before designing. The old website is found here: https://qp-fiduciary.example/

Target Market(s)

Actuaries and associated businesses internationally

Industry/Entity Type

professional services - actuaries

Number of Pages Required

3 page

Font styles to use
Sans Serif

Colors
0054AA
0677BA
7BADD7
CADEEF
E8F1F8
0094D4
00A9DD
6FCCEA
C7EBF8
E9F6FB
F0912C
F2A743
F7CA91
FBE8D2
FDF5EE
EE7325
F08F49
F5BC92
FAE3D3
FDF4ED
EB3D1F
EC4F4E
F09395
F8D3D4
FCEDEE

Requirements
Must have
• blues and greens to match the logo color, complimentary colors, navigation
Nice to have
• old site: https://qp-fiduciary.example/

```html
<!DOCTYPE html>
<html lang="en">
<head>
<meta charset="utf-8">
<title>QP Fiduciary — Actuarial Software</title>
<link href="https://fonts.googleapis.com/css2?family=Michroma&family=Lexend:wght@300;400;500;600&display=swap" rel="stylesheet">
<style>
:root{
  --blue:#0D4FEA;
  --navy:#0054AA;
  --sky:#0094D4;
  --orange:#EE7325;
  --orange-soft:#F7CA91;
  --hero-bg:#F3F6FD;
  --ink:#111418;
  --muted:#9AA0A8;
  --line:#D7DAE0;
  --green:#0FAE7E;
  --teal:#20B69A;
  --amber:#F5A81C;
  --coral:#EE6A2E;
  --violet:#7A55B4;
  --white:#FFFFFF;
}
*{margin:0;padding:0;box-sizing:border-box}
html,body{width:1200px;height:3331px;overflow:hidden}
body{position:relative;background:var(--white);font-family:"Lexend",sans-serif;font-weight:300;color:var(--ink)}
.abs{position:absolute}
.display{font-family:"Michroma",sans-serif;font-weight:400;text-transform:uppercase;letter-spacing:0}

/* header */
.site-header{left:0;top:0;width:1200px;height:58px;background:var(--white);z-index:5}
.brand{font-family:"Michroma",sans-serif;font-size:18px;color:var(--ink);display:flex;align-items:center;gap:10px;white-space:nowrap}
.brand-dot{width:12px;height:12px;border-radius:50%;background:var(--orange)}
.site-header .brand{position:absolute;left:150px;top:17px}
.main-nav{position:absolute;right:270px;top:26px;display:flex;align-items:center;gap:22px;font-size:9.5px;font-weight:400;letter-spacing:.02em;white-space:nowrap}
.main-nav .home{width:10px;height:10px}
.user-icon{position:absolute;left:958px;top:22px}
.header-cta{position:absolute;left:990px;top:0;width:210px;height:58px;background:var(--blue);border-bottom-left-radius:40px;color:var(--white);font-size:9.5px;font-weight:600;padding:18px 0 0 30px;line-height:1.15;white-space:nowrap}
.header-cta .arrow{position:absolute;right:14px;top:24px}

/* hero */
.hero-bg{left:0;top:0;width:1200px;height:856px;background:var(--hero-bg);border-radius:0 0 120px 120px}
.hero-title{left:0;top:158px;width:1200px;text-align:center;font-size:30px;line-height:40px}
.hero-sub{left:0;top:292px;width:1200px;text-align:center;font-size:11px;line-height:16px;color:#333}
.text-link{font-size:10px;font-weight:600;color:var(--orange);letter-spacing:.02em}
.hero-link{left:0;top:342px;width:1200px;text-align:center}
.mosaic{left:225px;top:432px;width:753px;height:198px;background:linear-gradient(90deg,#B8CFEE 0%,#1E7AC8 20%,#5FD2C5 40%,#1459B8 55%,#F0A53A 68%,#D5E4F4 85%,#F09A3A 100%)}

/* overview */
.overview{left:150px;top:630px;width:899px;height:372px;background:var(--white);border-radius:50px;box-shadow:0 20px 40px rgba(30,50,110,.08)}
.overview h2{position:absolute;left:84px;top:110px;font-size:23px;line-height:31px}
.overview p{position:absolute;left:84px;top:178px;width:340px;font-size:14.5px;line-height:23px;color:#222}
.overview-diagram{position:absolute;left:531px;top:46px;width:254px;height:268px;border-radius:20px;background:radial-gradient(circle at 60% 40%,#F28A2E 0%,#2E63E0 45%,#FFFFFF 80%)}

/* core solutions */
.vline{width:1px;background:var(--line)}
.hline{height:1px;background:var(--line)}
.core-title{left:0;top:1074px;width:1200px;text-align:center;font-size:23px}
.solution-hl{left:459px;top:1156px;width:304px;height:370px;border-top-left-radius:80px;background:linear-gradient(160deg,#F9C69A 0%,#FDEBDC 35%,#FFFFFF 75%)}
.corner-dot{width:7px;height:7px;background:var(--blue)}
.solution{width:240px}
.solution svg{display:block}
.solution h3{font-family:"Michroma",sans-serif;font-weight:400;font-size:14px;line-height:19px;text-transform:uppercase;margin-top:40px}
.solution p{font-size:13px;line-height:21px;margin-top:10px;color:#222}

/* characteristics */
.traits{left:0;top:1646px;width:1200px;height:503px;background:var(--blue);border-top-left-radius:90px}
.traits h2{position:absolute;left:0;top:95px;width:1200px;text-align:center;font-size:23px;color:var(--white)}
.trait{position:absolute;text-align:center;color:var(--white);font-size:13.5px;line-height:21px}
.trait .badge{width:90px;height:90px;border-radius:50%;margin:0 auto 18px;display:flex;align-items:center;justify-content:center}
.hub{left:519px;top:2060px;width:160px;height:160px;border-radius:50%;background:var(--white)}

/* insights */
.insights-title{left:0;top:2262px;width:1200px;text-align:center;font-size:23px}
.card{position:absolute;top:2325px;width:291px}
.card .thumb{height:213px;border-radius:22px;position:relative}
.tag{position:absolute;left:16px;top:16px;background:var(--white);border-radius:12px;font-size:8px;font-weight:600;padding:5px 12px}
.card .date{font-size:10px;color:var(--muted);margin-top:24px}
.card h3{font-family:"Michroma",sans-serif;font-weight:400;font-size:12px;line-height:18px;text-transform:uppercase;margin-top:10px}
.btn{display:flex;align-items:center;justify-content:center;border-radius:20px;font-size:9.5px;font-weight:600;white-space:nowrap}
.btn-orange{left:535px;top:2674px;width:132px;height:40px;background:var(--orange);color:var(--white)}

/* cta */
.cta{left:0;top:2795px;width:1200px;height:219px;background:linear-gradient(120deg,#0DA772 0%,#10B58E 55%,#0C9F72 100%);border-top-right-radius:80px}
.cta h2{position:absolute;left:151px;top:88px;font-size:28px;line-height:33px;color:var(--white)}
.btn-white{position:absolute;left:828px;top:91px;width:221px;height:39px;background:var(--white);color:var(--ink);font-size:8.5px}

/* footer */
.footer-col{top:3108px}
.footer-col h4{font-family:"Michroma",sans-serif;font-weight:400;font-size:11.5px;text-transform:uppercase;margin-bottom:10px}
.footer-col li{list-style:none;font-size:10.5px;line-height:22px;color:#333;display:flex;align-items:center;gap:6px}
.social{width:16px;height:16px;border-radius:50%;background:#D9DCE2;margin-top:4px}
.footer-brand{left:0;top:3235px;width:1200px;justify-content:center}
.copyright{left:0;top:3280px;width:1200px;text-align:center;font-size:10.5px;color:#444}
</style>
</head>
<body>

<div class="abs hero-bg"></div>

<header class="abs site-header">
  <div class="brand"><span>QP FIDUCIARY</span><span class="brand-dot"></span></div>
  <nav class="main-nav">
    <svg class="home" viewBox="0 0 10 10"><path d="M5 1 L9 5 H8 V9 H2 V5 H1 Z" fill="var(--blue)"/></svg>
    <span>PLATFORM</span><span>SOLUTIONS</span><span>INSIGHTS</span><span>COMPANY</span><span>CONTACT</span>
  </nav>
  <svg class="user-icon" width="14" height="14" viewBox="0 0 14 14" fill="none" stroke="#333"><circle cx="7" cy="5" r="3"/><path d="M2 13c0-3 2-5 5-5s5 2 5 5"/></svg>
  <a class="header-cta">REQUEST A<br>TECHNICAL WALKTHROUGH
    <svg class="arrow" width="10" height="8" viewBox="0 0 10 8" fill="none" stroke="#fff"><path d="M0 4H9M6 1l3 3-3 3"/></svg>
  </a>
</header>

<h1 class="abs display hero-title">Actuarial software<br>for structured, auditable<br>financial analysis</h1>
<p class="abs hero-sub">Software that translates actuarial methodologies into disciplined decision-ready analytical tools<br>across diverse regulatory environments.</p>
<div class="abs hero-link"><span class="text-link">REQUEST A&nbsp; TECHNICAL WALKTHROUGH &nbsp;→</span></div>
<div class="abs mosaic" role="img" aria-label="Geometric mosaic pattern of blue, teal, violet and orange shapes"></div>

<section class="abs overview">
  <h2 class="display">Platform<br>overview</h2>
  <p>QP Fiduciary develops modular actuarial software designed to support reserving, valuation, pricing, and risk analysis workflows across diverse regulatory environments.</p>
  <div class="overview-diagram" role="img" aria-label="Illustrated diagram of platform modules: data integration, valuation, pricing, reserving and risk analysis"></div>
</section>

<div class="abs vline" style="left:151px;top:1002px;height:644px"></div>
<div class="abs vline" style="left:1046px;top:1002px;height:644px"></div>
<h2 class="abs display core-title">Core solutions</h2>
<div class="abs hline" style="left:0;top:1156px;width:1200px"></div>
<div class="abs hline" style="left:0;top:1526px;width:1200px"></div>
<div class="abs solution-hl"></div>
<div class="abs corner-dot" style="left:152px;top:1156px"></div>
<div class="abs corner-dot" style="left:1039px;top:1519px"></div>

<div class="abs solution" style="left:204px;top:1232px">
  <svg width="80" height="78" viewBox="0 0 80 78" fill="none" stroke="#111" stroke-width="2"><circle cx="18" cy="24" r="14"/><path d="M18 16v16M14 20h6a3 3 0 010 6h-4a3 3 0 000 6h6"/><circle cx="56" cy="14" r="8"/><circle cx="56" cy="14" r="3"/><path d="M18 38v24M12 62h12v12H12zM34 74V58h7v16M46 74V48h7v26M58 74V40h7v34"/></svg>
  <h3>Reserving &amp;<br>valuation</h3>
  <p>Software supporting structured reserving workflows and financial reporting across jurisdictions.</p>
</div>
<div class="abs solution" style="left:522px;top:1232px">
  <svg width="90" height="78" viewBox="0 0 90 78" fill="none" stroke="#111" stroke-width="2"><circle cx="24" cy="20" r="14"/><circle cx="62" cy="28" r="12"/><path d="M24 12v16M62 21v14"/><path d="M8 50c10-6 20-6 30 2l14 2c4 1 4 6 0 6H36M52 58l18-8c4-2 7 3 3 6L52 70H24l-12-6"/></svg>
  <h3>QP Fiduciary<br>pricing</h3>
  <p>Models supporting insurance and reinsurance pricing based on actuarial methodologies.</p>
</div>
<div class="abs solution" style="left:806px;top:1232px">
  <svg width="90" height="78" viewBox="0 0 90 78" fill="none" stroke="#111" stroke-width="2"><circle cx="20" cy="22" r="12"/><circle cx="20" cy="22" r="5"/><path d="M58 6L76 38H40Z"/><path d="M58 17v10M58 31v2"/><path d="M4 52h12v18H4zM16 54l20-4c6 0 8 4 4 6l-14 3M40 56l22-4c4 0 5 4 1 6L30 68H16"/></svg>
  <h3>Enterprise risk<br>management</h3>
  <p>Software supporting reinsur-<br>ance optimization and<br>capital modeling.</p>
</div>

<section class="abs traits">
  <h2 class="display">Platform characteristics</h2>
  <div class="trait" style="left:147px;top:176px;width:220px">
    <div class="badge" style="background:var(--teal)"><svg width="40" height="36" viewBox="0 0 40 36" fill="none" stroke="#fff" stroke-width="1.6"><rect x="14" y="2" width="12" height="9"/><path d="M20 11v7M6 18h28M6 18v6M20 18v6M34 18v6"/><rect x="2" y="24" width="8" height="8"/><rect x="16" y="24" width="8" height="8"/><rect x="30" y="24" width="8" height="8"/></svg></div>
    Structured workflows suitable for multi-jurisdictional review
  </div>
  <div class="trait" style="left:400px;top:176px;width:210px">
    <div class="badge" style="background:var(--amber)"><svg width="40" height="40" viewBox="0 0 40 40" fill="none" stroke="#fff" stroke-width="1.6"><circle cx="20" cy="18" r="10"/><circle cx="20" cy="18" r="4"/><path d="M4 34h30l-4-4M4 34l4 4"/></svg></div>
    Transparent assumptions and methodological clarity
  </div>
  <div class="trait" style="left:634px;top:176px;width:160px">
    <div class="badge" style="background:var(--coral)"><svg width="38" height="40" viewBox="0 0 38 40" fill="none" stroke="#fff" stroke-width="1.6"><rect x="6" y="4" width="22" height="30"/><path d="M12 12h10M12 18h10M12 24h6"/><circle cx="28" cy="30" r="5"/><path d="M24 38h10"/></svg></div>
    Comparative scenario analysis
  </div>
  <div class="trait" style="left:828px;top:176px;width:220px">
    <div class="badge" style="background:var(--violet)"><svg width="40" height="40" viewBox="0 0 40 40" fill="none" stroke="#fff" stroke-width="1.6"><circle cx="20" cy="18" r="6"/><path d="M9 36c0-7 5-11 11-11s11 4 11 11M20 4v4M8 8l3 3M32 8l-3 3M4 18h4M32 18h4"/></svg></div>
    Supports professional judgment rather than replacing it
  </div>
  <svg class="abs" style="left:0;top:0" width="1200" height="503" fill="none" stroke="rgba(255,255,255,.7)" stroke-width="1" stroke-dasharray="3 3">
    <path d="M257 338v30h285v60M494 338v30M714 338v30h-70v60M927 338v30H606"/>
    <path d="M542 368h64v64"/>
    <g fill="#fff" stroke="none"><circle cx="257" cy="338" r="2.5"/><circle cx="494" cy="338" r="2.5"/><circle cx="714" cy="338" r="2.5"/><circle cx="927" cy="338" r="2.5"/><circle cx="542" cy="414" r="2.5"/><circle cx="606" cy="408" r="2.5"/><circle cx="644" cy="414" r="2.5"/></g>
  </svg>
</section>
<div class="abs hub"></div>

<h2 class="abs display insights-title">Insights</h2>
<article class="card" style="left:151px">
  <div class="thumb" style="background:linear-gradient(180deg,#2E2E2E,#3A3A3A)" role="img" aria-label="Dark financial chart with candlestick lines"><span class="tag">ARTICLE</span></div>
  <p class="date">25-01-2026</p>
  <h3>Methodological perspectives in actuarial reserving</h3>
</article>
<article class="card" style="left:455px">
  <div class="thumb" style="background:linear-gradient(120deg,#B9D2F0 0%,#5A86D6 50%,#2A3B9C 80%,#8E5BC8 100%)" role="img" aria-label="Abstract swirling blue and violet ribbon shapes"><span class="tag">ARTICLE</span></div>
  <p class="date">11-02-2026</p>
  <h3>Governance considerations in multi-jurisdictional analysis</h3>
</article>
<article class="card" style="left:758px">
  <div class="thumb" style="background:linear-gradient(135deg,#7DC6C0 0%,#4E9EA8 45%,#D8503A 60%,#6FB7B6 100%)" role="img" aria-label="Stylised illustration of a figure in red among teal shards"><span class="tag">ARTICLE</span></div>
  <p class="date">17-03-2026</p>
  <h3>Observations on actuarial practice in emerging markets</h3>
</article>
<a class="abs btn btn-orange">READ INSIGHTS</a>

<section class="abs cta">
  <h2 class="display">Interested in exploring<br>the platform?</h2>
  <a class="btn btn-white">REQUEST TECHNICAL WALKTHROUGH</a>
</section>

<footer>
  <div class="abs footer-col" style="left:151px"><h4>Company</h4><ul><li>About Us</li><li>Team</li><li>Careers</li></ul></div>
  <div class="abs footer-col" style="left:343px"><h4>Platform</h4><ul><li>Features</li><li>Pricing</li></ul></div>
  <div class="abs footer-col" style="left:530px"><h4>Solutions</h4><ul><li>For Businesses</li><li>For Actuaries</li></ul></div>
  <div class="abs footer-col" style="left:738px"><h4>Insights</h4><ul><li>Blog</li><li>Case Studies</li></ul></div>
  <div class="abs footer-col" style="left:927px"><h4>Contact</h4><ul>
    <li><svg width="9" height="7" viewBox="0 0 9 7"><rect width="9" height="7" fill="var(--orange)"/><path d="M0 0l4.5 4L9 0" stroke="#fff" fill="none"/></svg>info@example.com</li>
    <li><svg width="8" height="8" viewBox="0 0 8 8"><path d="M1 0h2l1 2-1 1c1 1 1 2 2 2l1-1 2 1v2C4 7 1 4 1 0z" fill="var(--orange)"/></svg>+1 234 567 890</li>
    <li><span class="social"></span></li>
  </ul></div>
  <div class="abs brand footer-brand"><span>QP FIDUCIARY</span><span class="brand-dot"></span></div>
  <p class="abs copyright">© 2026 QP Fiduciary. All rights reserved.</p>
</footer>

</body>
</html>
```